Website homepage rework for women's travel website

I have a homepage (http://www.ladies-at-the-helm.com) that I'm 50% happy with but don't want to completely overhaul. I'd like to retain a similar look but upgrade it to something a bit more modern and less old-fashioned. The basic sense of the site is empowering, self-confident, fun and adventurous - but female and over 40.

A number of the elements on the page have to be redesigned, a few can be tweaked, and a few left alone. See the rest of the brief for further information.

Target Market(s)

women over 40 who like to travel

Industry/Entity Type

Travel

Number of Pages Required

1 page

Font styles to use
Other font styles liked:
• see my brief

Requirements
Must have
• - size - the page must be significantly wider
• - the only font I MUST keep is Raleway (as in the tagline) and possibly the font of the site name (Ladies at the Helm). Both of those work for me. There are too many fonts on the page, however, and that needs to be unified.
• - the rectangles I click to get inside the site have to change to something more modern, possibly square - they do not have to be separated into two columns as they are now, nor do they need the titles (toolkit etc)
• - I like the background image of the header - but it needs to be wider of course - also keep in mind the aspect - it has to fit into the smaller inside pages, whose size will not change
• - at the end of the project I need to receive the separate elements of the design so I can eventually make a change myself if needed ie. replace my own photo, for example
Nice to have
• - the three photos need to change to something more eye-popping - or something else should take their place to fill the space
Should not have
• I do not want a full, original redesign. I want my readers to still feel as though they are on the same site - same header, mostly same fonts.

```html
<!DOCTYPE html>
<html lang="en">
<head>
<meta charset="utf-8">
<title>Ladies at the Helm – For women who travel smart, safe + solo</title>
<link rel="stylesheet" href="https://fonts.googleapis.com/css2?family=Raleway:wght@400;500;600;700&family=Oswald:wght@400;500&display=swap">
<style>
:root{
  --ink:#222222;
  --text:#555555;
  --muted:#777777;
  --nav:#2e2e2e;
  --nav-active:#474747;
  --red:#d7261c;
  --red-dark:#c4161c;
  --orange:#f28a12;
  --amber:#f5a51c;
  --purple:#7e4a9c;
  --green:#5cb512;
  --green-dark:#4f9e1e;
  --slate:#414a55;
  --news-bg:#efefef;
  --line:#dddddd;
  --white:#ffffff;
}
*{box-sizing:border-box;margin:0;padding:0}
html,body{width:1200px;height:2597px;overflow:hidden}
body{font-family:"Raleway",Arial,sans-serif;color:var(--text);background:var(--white);position:relative}
a{color:inherit;text-decoration:none}

/* Hero */
.hero{position:absolute;left:0;top:0;width:1200px;height:554px;
  background:linear-gradient(180deg,#f2b21c 0%,#ef8a18 38%,#c9581c 62%,#b98a5a 78%,#8a7b5e 100%)}
.hero-photo{position:absolute;inset:0;
  background:radial-gradient(ellipse 230px 300px at 230px 330px,#e8d8c6 0%,#dcc3a8 45%,rgba(220,195,168,0) 100%),
  linear-gradient(100deg,rgba(255,210,90,.35),rgba(180,70,20,.15))}
.brand-panel{position:absolute;left:627px;top:66px;width:468px;height:90px;background:rgba(255,244,214,.72);padding:6px 14px}
.brand-name{display:block;font-family:"Raleway",Arial,sans-serif;font-weight:500;font-size:44px;line-height:50px;color:var(--red-dark);text-align:right}
.brand-tagline{display:block;font-size:22px;line-height:28px;color:#3a3a3a;text-align:right}
.promo{position:absolute;left:719px;top:263px;width:327px;height:222px;background:var(--red);border:3px solid rgba(255,255,255,.75);padding:22px 22px 0 26px;color:var(--white)}
.promo-title{font-family:"Oswald",Arial,sans-serif;font-weight:500;font-size:38px;line-height:42px;letter-spacing:.5px}
.promo-sub{font-family:"Oswald",Arial,sans-serif;font-size:28px;line-height:34px}
.promo-btn{display:inline-block;margin-top:16px;border:1.5px solid var(--white);padding:7px 16px;font-size:13px;font-weight:600;letter-spacing:.6px}
.dots{position:absolute;left:26px;bottom:18px;display:flex;gap:8px;align-items:center}
.dots span{width:9px;height:9px;border-radius:50%;background:var(--white)}
.dots span.on{width:14px;height:14px;background:transparent;border:2px solid var(--white);position:relative}
.dots span.on::after{content:"";position:absolute;left:2px;top:2px;width:6px;height:6px;border-radius:50%;background:var(--white)}

/* Nav */
.main-nav{position:absolute;left:0;top:554px;width:1200px;height:70px;background:var(--nav)}
.main-nav ul{list-style:none;display:flex;margin-left:97px;height:70px}
.main-nav li{height:70px;display:flex;flex-direction:column;align-items:center;justify-content:center;gap:7px;color:var(--white);font-size:14px;font-weight:500;border-right:1px solid #444;padding:0 26px}
.main-nav li.active{background:var(--nav-active)}
.main-nav li:last-child{border-right:none}
.main-nav svg{width:22px;height:20px;fill:none;stroke:var(--white);stroke-width:1.8}

/* Intro */
.intro{position:absolute;left:0;top:624px;width:1200px;height:299px}
.polaroids{position:absolute;left:139px;top:69px;width:415px;height:164px;display:flex;gap:10px;align-items:center}
.polaroid{background:var(--white);padding:8px 8px 20px;box-shadow:0 2px 6px rgba(0,0,0,.35)}
.polaroid div{width:118px;height:100px}
.polaroid.p1{transform:rotate(-3deg)}
.polaroid.p2{transform:rotate(4deg)}
.polaroid.p3{transform:rotate(-2deg)}
.p1 div{background:linear-gradient(180deg,#4da3d8,#7cc6e4 55%,#d9c8a0)}
.p2 div{background:linear-gradient(160deg,#e97f2c,#3a8fb0 55%,#4e8e4a)}
.p3 div{background:linear-gradient(180deg,#c56b3d,#8a9b68 60%,#b23a2a)}
.intro-text{position:absolute;left:610px;top:77px;width:500px}
.intro-text h1{font-size:19px;line-height:30px;font-weight:600;color:var(--ink);letter-spacing:.3px}
.intro-text ul{list-style:none;margin-top:16px}
.intro-text li{font-size:14px;line-height:27px;color:#444;display:flex;align-items:center;gap:10px}
.intro-text li svg{width:12px;height:12px;fill:#333}
.intro-text b{font-weight:700;color:var(--ink)}

/* Subscribe band */
.cta{position:absolute;left:99px;top:923px;width:1002px;height:101px;background:var(--slate);overflow:hidden}
.cta-accent{position:absolute;right:0;top:0;width:310px;height:101px;background:var(--orange);clip-path:polygon(35px 0,100% 0,100% 100%,0 100%)}
.cta h2{position:absolute;left:28px;top:20px;color:var(--white);font-size:28px;line-height:32px;font-weight:600}
.cta p{position:absolute;left:28px;top:56px;color:var(--white);font-size:22px;font-weight:600}
.cta p u{text-underline-offset:3px}
.cta-btn{position:absolute;right:32px;top:30px;background:var(--slate);color:var(--white);font-size:15px;font-weight:600;padding:11px 22px;border-radius:2px;display:flex;align-items:center;gap:6px}
.cta-btn svg{width:14px;height:14px}

/* Tile grids */
.section-title{position:absolute;left:0;width:1200px;text-align:center;font-size:30px;font-weight:500;color:var(--ink);letter-spacing:.5px}
.tiles{position:absolute;left:99px;width:1003px;display:flex;gap:12px}
.tile{width:242px;height:288px}
.tile-img{width:242px;height:229px}
.tile-label{height:59px;padding:9px 12px 0;color:var(--white)}
.tile-label strong{display:block;font-size:17px;font-weight:700;line-height:21px}
.tile-label span{display:block;font-size:12px;line-height:17px}
.bg-red{background:var(--red)}
.bg-purple{background:var(--purple)}
.bg-orange{background:var(--orange)}
.bg-green{background:var(--green)}
.bg-amber{background:var(--amber)}
.bg-green-dark{background:var(--green-dark)}
.img-dining{background:linear-gradient(160deg,#7a6a4a,#c9a176 45%,#5a4b38)}
.img-packing{background:linear-gradient(170deg,#6c6f80,#9b3a3a 45%,#3d3f50)}
.img-cruise{background:linear-gradient(180deg,#1f6fc9 0%,#6aa8e8 45%,#f1f4f7 60%,#2a6aa8 100%)}
.img-yoga{background:linear-gradient(180deg,#c9dde6,#5f8c72 45%,#8fa8b0 80%,#7d8f96)}
.img-glacier{background:linear-gradient(180deg,#2a73c6 0%,#8fb9e0 40%,#e8f1f8 62%,#7fa6c8 100%)}
.img-food{background:linear-gradient(160deg,#f3f0ea,#d9a65a 45%,#b07a3a 75%,#f0ede6)}
.img-hiker{background:linear-gradient(180deg,#3b78c2 0%,#f0c070 55%,#5b4a3a 100%)}
.img-castle{background:linear-gradient(180deg,#4d8ad0 0%,#b4502c 45%,#8e3a24 75%,#3c5a70 100%)}

/* News */
.news{position:absolute;left:0;top:1931px;width:1200px;height:333px;background:var(--news-bg)}
.news h2{position:absolute;left:99px;top:50px;font-size:21px;font-weight:500;color:var(--ink)}
.news-arrows{position:absolute;left:1056px;top:52px;display:flex;gap:12px}
.news-arrows svg{width:16px;height:14px;stroke:#333;stroke-width:1.6;fill:none}
.news-item{position:absolute;top:99px;width:500px;height:170px}
.news-item.one{left:99px}
.news-item.two{left:630px}
.news-img{position:absolute;left:0;top:0;width:186px;height:164px}
.img-waterfall{background:linear-gradient(160deg,#3f7a3a,#8ab86a 45%,#e9eef0 60%,#4b7d3e)}
.img-desert{background:linear-gradient(180deg,#d8c2a2,#b89674 50%,#8f7356)}
.news-body{position:absolute;left:213px;top:0;width:260px}
.news-body h3{font-size:17px;font-weight:500;color:#444;line-height:22px}
.news-date{margin-top:18px;font-size:13px;font-weight:600;color:var(--red)}
.news-body p{margin-top:12px;font-size:12px;line-height:17.5px;color:#555}
.read-more{display:block;margin-top:10px;font-size:13px;color:#333}

/* Footer */
.site-footer{position:absolute;left:0;top:2264px;width:1200px;height:333px;background:var(--white)}
.footer-brand{position:absolute;left:100px;top:85px;width:220px}
.footer-brand .name{display:block;font-size:24px;font-weight:500;line-height:28px;color:var(--red-dark)}
.footer-brand .tag{display:block;font-size:11px;color:#444;margin-top:3px}
.social{display:flex;gap:6px;margin-top:14px;margin-left:42px}
.social span{width:26px;height:26px;border-radius:50%;border:1.5px solid #555}
.footer-col{position:absolute;top:48px}
.footer-col h4{font-size:15px;font-weight:600;color:var(--ink);letter-spacing:.3px}
.col-news{left:376px;width:250px}
.col-news p{margin-top:12px;font-size:12px;line-height:19px;color:#444}
.email-field{margin-top:16px;width:242px;height:42px;border:1px solid var(--line);font-size:12px;color:#555;padding:13px 12px}
.subscribe-btn{display:inline-block;margin-top:14px;background:var(--red-dark);color:var(--white);font-size:13px;font-weight:600;padding:12px 14px}
.col-contact{left:705px;width:260px}
.contact-line{display:flex;gap:14px;font-size:13px;line-height:20px;color:#444;margin-top:20px}
.contact-line svg{width:14px;height:14px;flex:none;fill:#555;margin-top:3px}
.col-contact .first{margin-top:22px}
.col-links{left:996px;width:120px}
.col-links ul{list-style:none;margin-top:14px}
.col-links li{font-size:12px;line-height:22px;color:#444}
.bottom-bar{position:absolute;left:0;top:282px;width:1200px;height:51px;border-top:1px solid var(--line);text-align:center;font-size:12px;color:#555;padding-top:16px}
</style>
</head>
<body>

<header class="hero">
  <div class="hero-photo" role="img" aria-label="Smiling founder with sunglasses on her head, in front of a desert highway leading to red rock buttes under a golden sky"></div>
  <div class="brand-panel">
    <span class="brand-name">Ladies at the Helm</span>
    <span class="brand-tagline">For women who travel smart, safe + solo</span>
  </div>
  <div class="promo">
    <div class="promo-title">SOLO TRAVEL TIPS</div>
    <div class="promo-sub">for women like you...</div>
    <a class="promo-btn" href="#">MORE INFORMATION</a>
    <div class="dots"><span class="on"></span><span></span><span></span><span></span></div>
  </div>
</header>

<nav class="main-nav">
  <ul>
    <li class="active"><svg viewBox="0 0 24 22"><path d="M3 11 12 3l9 8M6 9v10h12V9M10 19v-5h4v5"/></svg>START HERE</li>
    <li><svg viewBox="0 0 24 22"><path d="M8 3 3 6l2 5 2-1v10h10V10l2 1 2-5-5-3c-1 2-2.5 3-4 3S9 5 8 3z"/></svg>ABOUT US</li>
    <li><svg viewBox="0 0 24 22"><path d="M12 2c1 0 1.5 1 1.5 2v5l7 4v2l-7-2v4l2 1.5V20L12 19l-3.5 1v-1.5l2-1.5v-4l-7 2v-2l7-4V4c0-1 .5-2 1.5-2z"/></svg>TRAVEL RESOURCES</li>
    <li><svg viewBox="0 0 24 22"><path d="M4 4h11a3 3 0 0 1 3 3v4a3 3 0 0 1-3 3H9l-4 3v-3H4a2 2 0 0 1-2-2V6a2 2 0 0 1 2-2zM18 8h2a2 2 0 0 1 2 2v4a2 2 0 0 1-2 2h-1v3l-3-3h-4"/></svg>BLOG</li>
    <li><svg viewBox="0 0 24 22"><path d="M3 3h8l10 10-8 8L3 11zM7 7h.1"/></svg>TRAVEL SHOP</li>
    <li><svg viewBox="0 0 24 22"><path d="M3 5h18v13H3zM3 5l9 7 9-7"/></svg>CONTACT US</li>
  </ul>
</nav>

<section class="intro">
  <div class="polaroids">
    <div class="polaroid p1"><div role="img" aria-label="Snapshot of palm trees on a tropical beach"></div></div>
    <div class="polaroid p2"><div role="img" aria-label="Snapshot of colourful potted plants against a painted wall"></div></div>
    <div class="polaroid p3"><div role="img" aria-label="Snapshot of a scooter in an old town street"></div></div>
  </div>
  <div class="intro-text">
    <h1>HI, I'M MARTA. I TOOK MY FIRST SOLO TRIP AT 15.<br>I'LL SHOW YOU HOW TO TRAVEL...</h1>
    <ul>
      <li><svg viewBox="0 0 24 24"><path d="M12 1c1 0 1.5 1 1.5 2v6l9 5v2.5l-9-3v5l2.5 2V23L12 22l-4 1v-2.5l2.5-2v-5l-9 3V14l9-5V3c0-1 .5-2 1.5-2z"/></svg><span><b>Smart</b>: practical tools to help you plan - and afford - the perfect trip</span></li>
      <li><svg viewBox="0 0 24 24"><path d="M12 1c1 0 1.5 1 1.5 2v6l9 5v2.5l-9-3v5l2.5 2V23L12 22l-4 1v-2.5l2.5-2v-5l-9 3V14l9-5V3c0-1 .5-2 1.5-2z"/></svg><span><b>Safe</b>: down-to-earth advice and a ton of safety recommendations</span></li>
      <li><svg viewBox="0 0 24 24"><path d="M12 1c1 0 1.5 1 1.5 2v6l9 5v2.5l-9-3v5l2.5 2V23L12 22l-4 1v-2.5l2.5-2v-5l-9 3V14l9-5V3c0-1 .5-2 1.5-2z"/></svg><span><b>Solo</b>: yes, you can do it!</span></li>
    </ul>
  </div>
</section>

<section class="cta">
  <div class="cta-accent"></div>
  <h2>THINKING OF SOLO TRAVEL?</h2>
  <p><u>CLICK HERE</u> TO FIND OUT HOW.</p>
  <a class="cta-btn" href="#">CLICK HERE to Subscribe <svg viewBox="0 0 16 16"><circle cx="8" cy="8" r="7.5" fill="#fff"/><path d="M6.5 4.5 10 8l-3.5 3.5" stroke="#414a55" stroke-width="2" fill="none"/></svg></a>
</section>

<h2 class="section-title" style="top:1072px">TRAVEL TOOLKIT</h2>
<div class="tiles" style="top:1147px">
  <a class="tile" href="#"><div class="tile-img img-dining" role="img" aria-label="Shared table with local dishes and drinks"></div><div class="tile-label bg-red"><strong>EATING WITH LOCALS</strong><span>The Ultimate Guide to Social Dining</span></div></a>
  <a class="tile" href="#"><div class="tile-img img-packing" role="img" aria-label="Travel gear laid out for packing"></div><div class="tile-label bg-purple"><strong>TRAVEL PACKING LIST</strong><span>Decide what to pack, for a weekend</span></div></a>
  <a class="tile" href="#"><div class="tile-img img-cruise" role="img" aria-label="White cruise ship on blue sea"></div><div class="tile-label bg-orange"><strong>NO SINGLE SUPPLEMENT</strong><span>These strategies can help you get</span></div></a>
  <a class="tile" href="#"><div class="tile-img img-yoga" role="img" aria-label="Woman in a yoga pose by a mountain lake"></div><div class="tile-label bg-green"><strong>STRESS MANAGEMENT</strong><span>Course for Travelers</span></div></a>
</div>

<h2 class="section-title" style="top:1484px">TRAVEL DESTINATIONS</h2>
<div class="tiles" style="top:1561px">
  <a class="tile" href="#"><div class="tile-img img-glacier" role="img" aria-label="Glacier and snowy mountains under a blue sky"></div><div class="tile-label bg-amber"><strong>SOLO IN ARGENTINA</strong><span>Does It Really Take Two to Tango?</span></div></a>
  <a class="tile" href="#"><div class="tile-img img-food" role="img" aria-label="Plate of fried fish with a lemon slice"></div><div class="tile-label bg-green-dark"><strong>EUROPEAN FOODIE</strong><span>Destinations for October</span></div></a>
  <a class="tile" href="#"><div class="tile-img img-hiker" role="img" aria-label="Backpacker on a rocky summit at sunrise"></div><div class="tile-label bg-red"><strong>SOLO WOMAN TRAVEL</strong><span>3-Week Central Asia Itinerary</span></div></a>
  <a class="tile" href="#"><div class="tile-img img-castle" role="img" aria-label="Red brick waterfront buildings beside a harbour"></div><div class="tile-label bg-green"><strong>REBELLIOUS GENEVA'S</strong><span>Geneva's Alter Ego?</span></div></a>
</div>

<section class="news">
  <h2>LATEST NEWS</h2>
  <div class="news-arrows">
    <svg viewBox="0 0 16 14"><path d="M15 7H2M6 2 1 7l5 5"/></svg>
    <svg viewBox="0 0 16 14"><path d="M1 7h13M10 2l5 5-5 5"/></svg>
  </div>
  <article class="news-item one">
    <div class="news-img img-waterfall" role="img" aria-label="Joyful woman with arms raised beside a waterfall"></div>
    <div class="news-body">
      <h3>Nulla at diam ornare, aliquam urna</h3>
      <div class="news-date">MAY 25, 2016</div>
      <p>Nulla at diam ornare, aliquam urna vel, commodo urna. Nam id risus a est luctus consectetur quis eget libero. Suspendisse potenti. Pellentesque habitant morbi tristique senectus</p>
      <a class="read-more" href="#">Read More +</a>
    </div>
  </article>
  <article class="news-item two">
    <div class="news-img img-desert" role="img" aria-label="Smiling hiker with backpack in a desert canyon"></div>
    <div class="news-body">
      <h3>Nulla at diam ornare, aliquam urna</h3>
      <div class="news-date">MAY 25, 2016</div>
      <p>Nulla at diam ornare, aliquam urna vel, commodo urna. Nam id risus a est luctus consectetur quis eget libero. Suspendisse potenti. Pellentesque habitant morbi tristique senectus</p>
      <a class="read-more" href="#">Read More +</a>
    </div>
  </article>
</section>

<footer class="site-footer">
  <div class="footer-brand">
    <span class="name">Ladies at the Helm</span>
    <span class="tag">For women who travel smart, safe + solo</span>
    <div class="social"><span></span><span></span><span></span><span></span></div>
  </div>
  <div class="footer-col col-news">
    <h4>SIGN UP FOR NEWSLETTER</h4>
    <p>Excepteur sint occaecat cupidatat non proident, sunt in culpa qui officia deserunt</p>
    <div class="email-field">Enter email</div>
    <a class="subscribe-btn" href="#">SUBSCRIPTION</a>
  </div>
  <div class="footer-col col-contact">
    <h4>CONTACT US</h4>
    <div class="contact-line first"><svg viewBox="0 0 24 24"><path d="M12 1a8 8 0 0 0-8 8c0 6 8 14 8 14s8-8 8-14a8 8 0 0 0-8-8zm0 11a3 3 0 1 1 0-6 3 3 0 0 1 0 6z"/></svg><span>Ladies at the Helm<br>14 Linden Court London N4 2QP</span></div>
    <div class="contact-line"><svg viewBox="0 0 24 24"><path d="M6 2 9.5 2 11 7 8.5 9a12 12 0 0 0 6.5 6.5l2-2.5 5 1.5V18a3 3 0 0 1-3 3C10 21 3 14 3 5a3 3 0 0 1 3-3z"/></svg><span>Phone: (480) 555-0192</span></div>
    <div class="contact-line"><svg viewBox="0 0 24 24"><path d="M2 5h20v14H2zm1.5 1.5L12 13l8.5-6.5" stroke="#fff" stroke-width="1.2"/></svg><span>info@ladies-at-the-helm.com</span></div>
  </div>
  <div class="footer-col col-links">
    <h4>QUICK LINKS</h4>
    <ul><li>Home</li><li>About</li><li>Travel Resources</li><li>Blog</li><li>Travel Shop</li><li>Contact</li></ul>
  </div>
  <div class="bottom-bar">©2015 - 2016 Ladies at the Helm. All Rights Reserved.</div>
</footer>

</body>
</html>
```